Tollin Waste Website Design

Our new start-up needs a website design. We plan to help businesses find more sustainable ways to manage their waste. Our initial website aims to gather contact data from potential business customers and comprehensive information from waste facilities and waste transporters. We have a logo design (attached) which we would like included in the website design. I have also attached a number of pages that describe what information should appear on each page as well as a web design brief file that describes the look we are after.

```html
<!DOCTYPE html>
<html lang="en">
<head>
<meta charset="utf-8">
<title>Tollin Waste</title>
<link rel="stylesheet" href="https://fonts.googleapis.com/css2?family=Montserrat:wght@400;600;700&family=Open+Sans:wght@400&display=swap">
<style>
  :root {
    --green: #7cb82f;
    --green-light: #9acb2e;
    --green-dark: #5f9a22;
    --nav-text: #3a3a3a;
    --logo-text: #3d3d3d;
    --white: #ffffff;
    --footer-bg: #1c1c1c;
    --footer-text: #9a9a9a;
    --footer-icon: #8a8a8a;
  }
  * { box-sizing: border-box; margin: 0; padding: 0; }
  html, body { width: 1200px; height: 614px; overflow: hidden; }
  body { font-family: "Montserrat", Arial, sans-serif; background: var(--white); position: relative; }

  .site-header { position: absolute; top: 0; left: 0; width: 1200px; height: 91px; background: var(--white); }
  .brand { position: absolute; left: 133px; top: 23px; display: flex; align-items: center; gap: 10px; text-decoration: none; }
  .brand-dot { width: 42px; height: 42px; border-radius: 50%; background: var(--green); }
  .brand-name { font-weight: 600; font-size: 24px; color: var(--logo-text); letter-spacing: 0.5px; }
  .main-nav { position: absolute; right: 132px; top: 35px; display: flex; gap: 37px; }
  .main-nav a { font-size: 15px; color: var(--nav-text); text-decoration: none; }
  .main-nav a.is-active { color: var(--green-dark); }

  .hero { position: absolute; top: 91px; left: 0; width: 1200px; height: 451px; overflow: hidden; }
  .hero-photo { position: absolute; inset: 0;
    background:
      linear-gradient(180deg, #2f5f95 0%, #3d6ea0 18%, #7a8590 40%, #a8abad 60%, #8b6a58 85%, #6e4a3c 100%); }
  .hero-shade { position: absolute; inset: 0; background: rgba(20, 20, 20, 0.25); }
  .hero-title { position: absolute; top: 289px; width: 100%; text-align: center; color: var(--white);
    font-weight: 700; font-size: 40px; letter-spacing: 0.3px; }
  .hero-subtitle { position: absolute; top: 339px; width: 100%; text-align: center; color: var(--white);
    font-weight: 600; font-size: 18px; }
  .audience-button { position: absolute; top: 377px; width: 297px; height: 50px; border-radius: 4px;
    background: linear-gradient(180deg, var(--green-light), var(--green-dark));
    color: var(--white); font-weight: 700; font-size: 19px; text-decoration: none;
    display: flex; align-items: center; justify-content: center;
    text-shadow: 0 1px 3px rgba(0,0,0,0.35); }
  .audience-button.producers { left: 132px; }
  .audience-button.facilities { left: 452px; }
  .audience-button.transporters { left: 771px; }

  .site-footer { position: absolute; top: 542px; left: 0; width: 1200px; height: 72px; background: var(--footer-bg);
    font-family: "Open Sans", Arial, sans-serif; color: var(--footer-text); font-size: 10.5px; }
  .footer-nav { position: absolute; left: 133px; top: 15px; display: flex; gap: 10px; }
  .footer-nav a { color: var(--footer-text); text-decoration: none; }
  .footer-nav .divider { color: var(--footer-text); }
  .copyright { position: absolute; left: 133px; top: 42px; }
  .social-links { position: absolute; left: 1016px; top: 28px; display: flex; gap: 18px; }
  .social-links span { width: 16px; height: 16px; border-radius: 50%; background: var(--footer-icon); display: block; }
</style>
</head>
<body>
  <header class="site-header">
    <a class="brand" href="#">
      <span class="brand-dot"></span>
      <span class="brand-name">Tollin Waste</span>
    </a>
    <nav class="main-nav">
      <a href="#" class="is-active">About us</a>
      <a href="#">What we do</a>
      <a href="#">Resources</a>
      <a href="#">Contact us</a>
    </nav>
  </header>

  <section class="hero">
    <div class="hero-photo" role="img" aria-label="Skip full of discarded industrial batteries in front of stacked blue and green drums on pallets"></div>
    <div class="hero-shade"></div>
    <h1 class="hero-title">WELCOME TO TOLLIN WASTE</h1>
    <p class="hero-subtitle">Take control of your waste here:</p>
    <a class="audience-button producers" href="#">WASTE PRODUCERS</a>
    <a class="audience-button facilities" href="#">WASTE FACILITIES</a>
    <a class="audience-button transporters" href="#">WASTE TRANSPORTERS</a>
  </section>

  <footer class="site-footer">
    <nav class="footer-nav">
      <a href="#">About us</a><span class="divider">|</span>
      <a href="#">What we do</a><span class="divider">|</span>
      <a href="#">Resources</a><span class="divider">|</span>
      <a href="#">Contact us</a>
    </nav>
    <p class="copyright">Copyright &copy;&nbsp; 2018&nbsp; Tollin Waste Management.&nbsp;&nbsp; All rights reserved.</p>
    <div class="social-links">
      <span role="img" aria-label="Social profile link"></span>
      <span role="img" aria-label="Video channel link"></span>
    </div>
  </footer>
</body>
</html>
```